Dental specialist needs a sharp looking letterhead

I am looking for a letterhead to be used to send letters and communication between myself (a dental specialist) and other dentists.
My office is a state of the art dental specialty office.
I need to letterhead to also state:
Bertram L. Oswick DDS
2748 Tollard Avenue, Suite K
West Tollard, NY 14391
(716)392-5061
fax: (716)392-5087
oswickroot.com (**this email address may change)

i included my logo designs.
thank you

Target Market(s)

dentists

Industry/Entity Type

Communication

Requirements
Must have
• the included logo, whether the vertical or horizontal versions

```html
<!DOCTYPE html>
<html lang="en">
<head>
<meta charset="utf-8">
<title>Meridian Endodontics P.C. – Letterhead</title>
<link href="https://fonts.googleapis.com/css2?family=Noto+Serif:wght@400;700&family=Roboto+Condensed:wght@400&display=swap" rel="stylesheet">
<style>
  :root{
    --backdrop:#ebebeb;
    --paper:#ffffff;
    --ink:#1c1c1c;
    --black-band:#000000;
    --blue:#1e88d0;
    --green:#7ab51d;
  }
  *{margin:0;padding:0;box-sizing:border-box}
  html,body{width:1200px;height:968px;overflow:hidden}
  body{background:var(--backdrop);position:relative;font-family:"Noto Serif",serif}

  .letterhead{
    position:absolute;left:280px;top:31px;width:640px;height:906px;
    background:var(--paper);
    box-shadow:0 4px 18px rgba(0,0,0,.12);
    overflow:hidden;
  }

  .brand{
    position:absolute;top:52px;left:0;right:0;
    display:flex;justify-content:center;align-items:center;gap:12px;
  }
  .brand-dot{width:30px;height:30px;border-radius:50%;background:var(--blue)}
  .brand-name{
    font-family:"Noto Serif",serif;font-weight:700;color:var(--ink);
    font-size:21px;line-height:1.15;letter-spacing:.04em;
  }
  .brand-name small{display:block;font-size:11px;letter-spacing:.12em}

  .doctor-tag{
    position:absolute;left:0;top:168px;width:178px;height:46px;
    background:var(--black-band);border-bottom:3px solid var(--blue);
    display:flex;align-items:center;padding-left:12px;
  }
  .doctor-name{font-family:"Noto Serif",serif;color:var(--green);font-size:13px;font-weight:400;white-space:nowrap}

  .contact-bar{
    position:absolute;left:0;right:0;bottom:58px;height:32px;
    font-family:"Roboto Condensed",sans-serif;font-size:9.5px;color:#fff;
  }
  .band{position:absolute;height:18px;display:flex;align-items:center;gap:10px;padding:0 8px}
  .band-blue{left:0;bottom:0;width:322px;background:var(--blue)}
  .band-green{left:370px;right:0;top:0;background:var(--green)}
  .footer-mark{position:absolute;left:336px;top:4px;width:24px;height:24px;border-radius:50%;background:var(--blue)}
  .item{display:flex;align-items:center;gap:4px;white-space:nowrap}
  .item svg{width:10px;height:10px;flex:none}
</style>
</head>
<body>
  <main class="letterhead">
    <header class="brand">
      <span class="brand-dot"></span>
      <div class="brand-name">MERIDIAN<small>Endodontics P.C.</small></div>
    </header>

    <div class="doctor-tag"><span class="doctor-name">Bertram L. Oswick DDS</span></div>

    <footer class="contact-bar">
      <div class="band band-blue">
        <span class="item">
          <svg viewBox="0 0 10 10"><circle cx="5" cy="5" r="5" fill="#fff"/><path d="M3.2 2.6l1 .9-.5.8c.4.8 1 1.4 1.8 1.8l.8-.5.9 1-.7.7C4.8 7 3 5.2 2.6 3.3z" fill="var(--blue)"/></svg>
          (716)392-5061
        </span>
        <span class="item">
          <svg viewBox="0 0 10 10"><circle cx="5" cy="5" r="5" fill="#fff"/><rect x="2.8" y="3.8" width="4.4" height="2.8" fill="var(--blue)"/><rect x="3.6" y="2.6" width="2.8" height="1.2" fill="var(--blue)"/></svg>
          (716)392-5087
        </span>
        <span class="item">
          <svg viewBox="0 0 10 10"><circle cx="5" cy="5" r="5" fill="#fff"/><rect x="2.6" y="3.2" width="4.8" height="3.6" fill="none" stroke="var(--blue)" stroke-width=".8"/><path d="M2.6 3.2L5 5.2l2.4-2" fill="none" stroke="var(--blue)" stroke-width=".8"/></svg>
          bertram@oswickroot.com
        </span>
      </div>
      <span class="footer-mark"></span>
      <div class="band band-green">
        <span class="item">
          <svg viewBox="0 0 10 10"><circle cx="5" cy="5" r="5" fill="#fff"/><path d="M5 2a2 2 0 0 1 2 2c0 1.4-2 3.8-2 3.8S3 5.4 3 4a2 2 0 0 1 2-2z" fill="var(--green)"/></svg>
          2748 Tollard Avenue, Suite K, West Tollard, NY 14391
        </span>
      </div>
    </footer>
  </main>
</body>
</html>
```